Business Card Design

I am a medical doctor who is also trained in eastern medicine and acupuncture. I would like to incorporate the chinese characters for "Balance" in a vertical configuration, prominently featured on the left hand side of the card. (see image that I tried to cut and paste together. There is also a horizontal version, but I would like the characters stacked. I included each character separately) I would like the chinese characters and my name to be in blue or teal with the other print either brown or black. I would like this tag line on the back of the card: "Balancing Western and Eastern Medicine to Achieve Optimal Health". I tried out a similar design in Prenvola Templates but the chinese characters said "sushi". Not exactly appropriate. Many thanks.

Industry/Entity Type

Medical

Contact Information for Business Card

Marianne Delvaro, MD, LAc
382-K Pelenaka St
Kailua, HI 96734
(808) 555-0147
mariannemdneedlecare@mailvora.net
www.mariannemdneedlecare.net

```html
<!DOCTYPE html>
<html lang="en">
<head>
<meta charset="utf-8">
<title>Marianne Delvaro, MD – Business Card</title>
<link rel="stylesheet" href="https://fonts.googleapis.com/css2?family=Josefin+Sans:wght@300&family=Raleway:wght@300&family=Arimo:wght@400&display=swap">
<style>
  :root {
    --page-bg: #ffffff;
    --card-edge: #2a140b;
    --card-brown: #3b2013;
    --card-brown-light: #4a2a19;
    --emblem-brown: #56301d;
    --teal: #3cc5d5;
    --teal-soft: #52cbd9;
    --teal-deep: #2fa9b8;
  }
  * { box-sizing: border-box; margin: 0; padding: 0; }
  html, body {
    width: 1200px;
    height: 900px;
    overflow: hidden;
    background: var(--page-bg);
  }
  .canvas {
    position: relative;
    width: 1200px;
    height: 900px;
  }
  .card {
    position: absolute;
    left: 260px;
    width: 680px;
    height: 388px;
    border-radius: 26px;
    border: 3px solid var(--card-edge);
    background: linear-gradient(100deg, var(--card-brown) 0%, var(--card-brown-light) 55%, var(--card-brown) 100%);
    overflow: hidden;
  }
  .card--back { top: 40px; }
  .card--front { top: 472px; }
  .card__frame {
    position: absolute;
    inset: 10px;
    border: 5px solid var(--teal);
    border-radius: 20px;
  }
  .card__emblem {
    position: absolute;
    width: 290px;
    height: 290px;
    border-radius: 50%;
    background: radial-gradient(circle, var(--emblem-brown) 0%, rgba(86, 48, 29, 0.55) 70%, rgba(86, 48, 29, 0) 100%);
    opacity: 0.8;
  }
  .card--back .card__emblem { left: 110px; top: 30px; }
  .card--front .card__emblem { left: 60px; top: 40px; }

  .tagline {
    position: absolute;
    left: 40px;
    right: 40px;
    top: 148px;
    text-align: center;
    font-family: "Josefin Sans", sans-serif;
    font-weight: 300;
    font-size: 27px;
    line-height: 1.3;
    letter-spacing: 0.5px;
    color: var(--teal);
  }

  .balance-mark {
    position: absolute;
    left: 44px;
    top: 40px;
    width: 118px;
    height: 250px;
    border-radius: 8px;
    background: linear-gradient(180deg, var(--teal) 0%, var(--teal-deep) 100%);
    opacity: 0.85;
  }
  .practitioner-name {
    position: absolute;
    left: 200px;
    top: 58px;
    font-family: "Raleway", sans-serif;
    font-weight: 300;
    font-size: 40px;
    color: var(--teal);
    white-space: nowrap;
  }
  .contact {
    position: absolute;
    right: 34px;
    top: 222px;
    text-align: right;
    font-family: "Arimo", sans-serif;
    color: var(--teal-soft);
    font-style: normal;
  }
  .contact__phone {
    font-size: 25px;
    margin-bottom: 6px;
  }
  .contact__line {
    font-size: 15px;
    line-height: 1.35;
  }
</style>
</head>
<body>
<main class="canvas">
  <section class="card card--back" aria-label="Card back">
    <div class="card__emblem" role="img" aria-label="Faint yin-yang emblem with acupuncture needle lines"></div>
    <div class="card__frame"></div>
    <p class="tagline">Balancing Western and Eastern Medicine<br>to Achieve Optimal Health</p>
  </section>

  <section class="card card--front" aria-label="Card front">
    <div class="card__emblem" role="img" aria-label="Faint yin-yang emblem with acupuncture needle lines"></div>
    <div class="card__frame"></div>
    <div class="balance-mark" role="img" aria-label="Brush-lettered Chinese characters for balance, stacked vertically"></div>
    <h1 class="practitioner-name">Marianne Delvaro, MD</h1>
    <address class="contact">
      <div class="contact__phone">(808) 555-0147</div>
      <div class="contact__line">mariannemdneedlecare@mailvora.net</div>
      <div class="contact__line">www.mariannemdneedlecare.net</div>
      <div class="contact__line">LAc 382-K Pelenaka St Kailua, HI 96734</div>
    </address>
  </section>
</main>
</body>
</html>
```